Brightmoor Essentials colloidal silver spray for pets.

We need a label for an 8-oz cobalt blue spray bottle. We are a small company just starting to share the benefits of colloidal silver. Our first offering will be the 8-oz spray bottle for pets. We would also like to update our logo. The finished project should be crisp and incorporate a dog on the label. I have attached the information we would like on the label and our logo, which can be changed to match your vision.
Updates

Hi, I would like to remind you that we are using a cobalt blue bottle with a black sprayer and would like an updated logo. Also, for the business cards, we don't want an animal on them, as we are planning future products for people. thank you

```html
<!DOCTYPE html>
<html lang="en">
<head>
<meta charset="utf-8">
<title>Brightmoor Essentials – Colloidal Silver Pet Spray Label</title>
<link rel="stylesheet" href="https://fonts.googleapis.com/css2?family=Antonio:wght@600;700&family=Oswald:wght@500;600&family=Arimo:wght@400&display=swap">
<style>
  :root {
    --page-bg: #f1f6e4;
    --silver-light: #f2f2f2;
    --silver-mid: #c9c9c9;
    --silver-dark: #a9a9a9;
    --navy: #2b2f8c;
    --cross-green: #20a656;
    --tick-green: #1f9e4b;
    --heading-grey: #2f2f2f;
    --body-grey: #2a2a2a;
    --tab-white: #ffffff;
    --brand-grey: #8a8a8a;
    --badge-red: #d8262c;
    --fur-dark: #7a3a12;
    --fur-light: #c8763a;
  }
  * { margin: 0; padding: 0; box-sizing: border-box; }
  html, body { width: 1200px; height: 1200px; overflow: hidden; }
  body { background: var(--page-bg); position: relative; }

  .label {
    position: absolute; left: 350px; top: 75px;
    width: 500px; height: 1050px; overflow: hidden;
    background: linear-gradient(90deg, var(--silver-dark) 0%, var(--silver-light) 45%, var(--silver-mid) 75%, var(--silver-dark) 100%);
  }

  .brand-tab {
    position: absolute; left: 160px; top: 0; width: 180px; height: 108px;
    background: var(--tab-white);
    clip-path: polygon(0 0, 100% 0, 100% 78%, 50% 100%, 0 78%);
    display: flex; flex-direction: column; align-items: center; justify-content: center;
    padding-bottom: 18px;
    font-family: "Oswald", sans-serif; font-weight: 600; color: var(--brand-grey);
    font-size: 19px; line-height: 1.05; text-transform: uppercase; letter-spacing: 0.5px; text-align: center;
  }

  .product-name {
    position: absolute; font-family: "Antonio", sans-serif; font-weight: 700;
    color: var(--navy); line-height: 1; white-space: nowrap; transform-origin: left top;
  }
  .product-name--colloidal { left: 119px; top: 118px; font-size: 122px; letter-spacing: 0; transform: scaleX(0.72); }
  .product-name--silver { left: 150px; top: 224px; font-size: 122px; letter-spacing: 2px; transform: scaleX(0.92); }

  .first-aid-cross { position: absolute; left: 36px; top: 212px; width: 100px; height: 100px; }

  .tagline {
    position: absolute; left: 0; width: 482px; text-align: center;
    font-family: "Oswald", sans-serif; font-weight: 600; color: var(--heading-grey);
    font-size: 46px; line-height: 1; white-space: nowrap;
  }
  .tagline--line1 { top: 376px; }
  .tagline--line2 { top: 432px; }

  .spec-grid {
    position: absolute; left: 60px; top: 492px;
    display: grid; grid-template-columns: 128px 26px auto; row-gap: 2px; align-items: center;
    font-family: "Arimo", sans-serif; font-size: 21px; color: var(--body-grey);
  }
  .spec-grid .spec-left { text-align: right; padding-right: 4px; }
  .spec-grid svg { width: 22px; height: 22px; }

  .origin-badge { position: absolute; left: 326px; top: 552px; width: 96px; height: 96px; }

  .pet-photo {
    position: absolute; left: 0; top: 545px; width: 310px; height: 505px;
    background: radial-gradient(ellipse at 50% 40%, var(--fur-light) 0%, var(--fur-dark) 70%, rgba(122,58,18,0) 100%);
    border-radius: 45% 45% 0 0;
  }

  .benefits {
    position: absolute; right: 32px; top: 676px; list-style: none; text-align: right;
    font-family: "Arimo", sans-serif; font-size: 22px; line-height: 31.6px; color: var(--body-grey);
  }

  .net-weight {
    position: absolute; right: 64px; top: 1003px;
    font-family: "Arimo", sans-serif; font-size: 18px; color: var(--body-grey);
  }
</style>
</head>
<body>
  <main class="label">
    <div class="brand-tab"><span>Brightmoor</span><span>Essentials</span></div>

    <svg class="first-aid-cross" viewBox="0 0 100 100" aria-hidden="true">
      <path d="M34 0h32v34h34v32H66v34H34V66H0V34h34z" fill="var(--cross-green)"/>
    </svg>
    <div class="product-name product-name--colloidal">COLLOIDAL</div>
    <div class="product-name product-name--silver">SILVER</div>

    <div class="tagline tagline--line1">NATURAL FIRST AID</div>
    <div class="tagline tagline--line2">FOR PETS</div>

    <div class="spec-grid">
      <span class="spec-left">10 PPM</span>
      <svg viewBox="0 0 22 22" aria-hidden="true"><circle cx="11" cy="11" r="10" fill="var(--tick-green)"/><path d="M6 11l4 4 7-9" stroke="#fff" stroke-width="2.6" fill="none" stroke-linecap="round"/></svg>
      <span>No preservatives</span>
      <span class="spec-left">100% pure</span>
      <svg viewBox="0 0 22 22" aria-hidden="true"><circle cx="11" cy="11" r="10" fill="var(--tick-green)"/><path d="M6 11l4 4 7-9" stroke="#fff" stroke-width="2.6" fill="none" stroke-linecap="round"/></svg>
      <span>No additives</span>
    </div>

    <div class="pet-photo" role="img" aria-label="Photo of a smiling orange Pomeranian dog sitting"></div>

    <svg class="origin-badge" viewBox="0 0 98 98" aria-hidden="true">
      <circle cx="49" cy="49" r="47" fill="#fff" stroke="#555" stroke-width="1.5"/>
      <circle cx="49" cy="49" r="30" fill="#fff" stroke="#999" stroke-width="1"/>
      <rect x="22" y="22" width="13" height="54" fill="var(--badge-red)"/>
      <rect x="63" y="22" width="13" height="54" fill="var(--badge-red)"/>
    </svg>

    <ul class="benefits">
      <li>Anti Microbial</li>
      <li>Anti Fungal</li>
      <li>Anti Bacterial</li>
      <li>Anti Viral</li>
      <li>Treats Burns</li>
      <li>Bites</li>
      <li>Cuts</li>
      <li>Abrasions</li>
      <li>Hots Spots</li>
    </ul>

    <div class="net-weight">Net Wight 8 oz</div>
  </main>
</body>
</html>
```